Quorva - corporate Business Card

We need a good look and innovative business card for a new start up company based in Los Angeles called "Quorva". We are in a payment business, including payment card, app, and ewallet. We are expert in online payment and Card not present (CNP) transaction.
We need an innovative, modern business card.

Our logo font is Aero Matics

Target Market(s)

Startup - Bank - Online Payment - Card Manufacturing

Industry/Entity Type

Startup

Contact Information for Business Card

phone: 555 014 7396 - Address: 4172 Marlowe blvd, Orlen Vista, NV 89299

Requirements
Must have
• Message: innovative, professional, expert, high tech, trust, online payment expert, security
Nice to have
• no comment
Should not have
• no Comment

```html
<!DOCTYPE html>
<html lang="en">
<head>
<meta charset="utf-8">
<title>Quorva — Business Card</title>
<link rel="stylesheet" href="https://fonts.googleapis.com/css2?family=Open+Sans:wght@400;600&display=swap">
<style>
  :root {
    --brand-red: #b71e2e;
    --paper: #ffffff;
    --ink: #555555;
    --ink-soft: #666666;
    --backdrop: #ece9e6;
  }
  * { margin: 0; padding: 0; box-sizing: border-box; }
  html, body { width: 1200px; height: 987px; overflow: hidden; }
  body {
    background: var(--backdrop);
    font-family: "Open Sans", Arial, sans-serif;
    position: relative;
  }
  .card {
    position: absolute;
    width: 615px;
    height: 352px;
    background: var(--paper);
    box-shadow: 0 2px 6px rgba(0,0,0,.18);
    overflow: hidden;
  }
  .card--front { left: 293px; top: 130px; }
  .card--back  { left: 292px; top: 505px; }

  .front-shape { position: absolute; inset: 0; width: 100%; height: 100%; }

  .brand { position: absolute; display: flex; align-items: center; }
  .brand__dot { border-radius: 50%; background: var(--brand-red); flex: none; }
  .brand__name { color: var(--brand-red); font-weight: 600; line-height: 1; letter-spacing: .5px; }

  .card--front .brand { left: 47px; top: 51px; }
  .card--front .brand__dot { width: 66px; height: 66px; margin-right: 12px; }
  .card--front .brand__name { font-size: 40px; }

  .holder { position: absolute; right: 91px; top: 150px; text-align: right; }
  .holder__name { color: var(--brand-red); font-size: 21px; font-weight: 600; line-height: 1.1; }
  .holder__title { color: var(--ink); font-size: 16px; line-height: 1.4; }

  .address { position: absolute; left: 47px; top: 182px; color: var(--ink); font-size: 16px; line-height: 23px; font-style: normal; }

  .contacts { position: absolute; left: 47px; top: 243px; list-style: none; color: var(--ink); font-size: 16px; }
  .contacts li { display: flex; align-items: center; height: 23px; }
  .contacts svg { width: 15px; height: 15px; margin-right: 11px; fill: var(--brand-red); flex: none; }

  .card--back .brand { left: 117px; top: 118px; }
  .card--back .brand__dot { width: 108px; height: 108px; margin-right: 22px; }
  .card--back .brand__name { font-size: 70px; }

  .web { position: absolute; left: 0; right: 0; top: 292px; text-align: center; color: var(--ink-soft); font-size: 15px; letter-spacing: 6px; }
</style>
</head>
<body>

<section class="card card--front">
  <svg class="front-shape" viewBox="0 0 615 352" preserveAspectRatio="none" aria-hidden="true">
    <rect x="330" y="0" width="285" height="352" fill="var(--brand-red)"/>
    <path d="M0 0 H448 C540 24 580 105 574 176 C568 270 492 346 398 352 H0 Z" fill="var(--paper)"/>
  </svg>

  <div class="brand">
    <span class="brand__dot"></span>
    <span class="brand__name">Quorva</span>
  </div>

  <div class="holder">
    <div class="holder__name">DANIEL REYES</div>
    <div class="holder__title">CEO&amp;Founder</div>
  </div>

  <address class="address">4172 Marlowe blvd<br>Orlen Vista, NV 89299</address>

  <ul class="contacts">
    <li>
      <svg viewBox="0 0 24 24"><path d="M6.6 10.8a15.1 15.1 0 0 0 6.6 6.6l2.2-2.2a1 1 0 0 1 1-.25 11.4 11.4 0 0 0 3.6.57 1 1 0 0 1 1 1V20a1 1 0 0 1-1 1A17 17 0 0 1 3 4a1 1 0 0 1 1-1h3.5a1 1 0 0 1 1 1c0 1.25.2 2.45.57 3.57a1 1 0 0 1-.25 1z"/></svg>
      555 014 7396
    </li>
    <li>
      <svg viewBox="0 0 24 24"><path d="M2 5h20v2l-10 6L2 7z"/><path d="M2 9l10 6 10-6v10H2z"/></svg>
      daniel@quorva.com
    </li>
    <li>
      <svg viewBox="0 0 24 24"><circle cx="12" cy="12" r="10"/><path d="M7 6c2 1 2 3 4 3s1 3 3 3 1 3-1 4M15 5c-1 2 1 3 3 3" fill="none" stroke="#fff" stroke-width="1.6"/></svg>
      www.quorva.com
    </li>
  </ul>
</section>

<section class="card card--back">
  <div class="brand">
    <span class="brand__dot"></span>
    <span class="brand__name">Quorva</span>
  </div>
  <div class="web">www.quorva.com</div>
</section>

</body>
</html>
```